Business Card - high end, modern health care

Hey designers!

We need a double sided business card for the boutique, cutting edge physical therapy rehabilitation centre in Sydney's Northern Beaches.

With the most qualified physios in the area The Harbourview Motion Clinic does what other physiotherapy practices do not, we take our time with our patients giving them longer appointments, better physios and therefor faster results!

We guarantee that the service people receive at THMC will be unparalleled.

Hence we need a business card to reflect our modern, boutique, high end service. The final design needs to reflect that we are in a class of our own yet with the feel of beachside retreat.

Below I have attached our logo in both blue on white and white on blue. The exact colour is;
and the font that we have used in our logo is Tex Gyre Aventador.

I like the idea of the blue as the main colour as it is more eye catching and our signage onto the main road will be in this blue and in the interest of consistency across marketing the blue needs to be a part of the design. However I would appreciate a few designs onto a wooden background as this is a visual theme within the fitout of the practice.

The design needs to be of standard size (91x55mm).

Target Market(s)

We target people who have an end outcome in mind and those who have had poor experiences with other providers and ensure that everyone gets the care that they deserve with a premium service that is tailored to the individuals circumstances. As a premium service, the target market is highly educated, business and tech savvy with the additional target market of elderly people who have self funded their retirement and see value in paying for the best ongoing rehabilitation to maintain independence.

Industry/Entity Type

Physical Therapy

Contact Information for Business Card

Name, designation( Titled Musculoskeletal Physiotherapist... there will also be those in the company that have multiple designations ie 5 or 6 words long), phone number, email, facebook, instagram, address

Font styles to use
Sans Serif

Colors

Designer to choose colors to be used in the design.

Requirements
Must have
• Front - The logo as large as possible, blue or wooden theme, and all of the important details.
• Back - A blank space/lines on which to write appointment times (no "Appointment, date, time" etc.)
Nice to have
• facebook url
• logos for facebook and instagram
• Mini logos for the phone and email?

```html
<!DOCTYPE html>
<html lang="en">
<head>
<meta charset="utf-8">
<title>The Harbourview Motion Clinic – Business Card</title>
<link href="https://fonts.googleapis.com/css2?family=Raleway:wght@400;500;600&display=swap" rel="stylesheet">
<style>
  :root {
    --brand-blue: #0c4a94;
    --ink: #1c1c1c;
    --paper: #f3f3f1;
    --rule: #2a2a2a;
    --backdrop: #9a9a9a;
    --social-fb: #2a8fd6;
    --social-ig: #e2558c;
  }
  * { box-sizing: border-box; margin: 0; padding: 0; }
  html, body { width: 1200px; height: 960px; overflow: hidden; }
  body {
    background: var(--backdrop);
    font-family: "Raleway", sans-serif;
    position: relative;
  }
  .card {
    position: absolute;
    width: 546px;
    height: 330px;
    box-shadow: 0 6px 18px rgba(0,0,0,.25);
  }

  /* Blue side */
  .card--brand {
    left: 600px; top: 90px;
    background: var(--brand-blue);
    display: flex; align-items: center; justify-content: center;
  }
  .brand-lockup { display: flex; align-items: center; gap: 16px; color: #fff; }
  .brand-lockup__dot { width: 50px; height: 50px; border-radius: 50%; background: #fff; flex: none; }
  .brand-lockup__name {
    font-weight: 600; font-size: 24px; line-height: 1.2;
    letter-spacing: 2px; text-transform: uppercase;
  }

  /* White side */
  .card--details {
    left: 60px; top: 480px;
    background: var(--paper);
    color: var(--ink);
  }
  .side-strip {
    position: absolute; left: 0; top: 0; width: 120px; height: 100%;
    border-right: 1.5px solid var(--rule);
  }
  .side-strip__lockup {
    position: absolute; left: 50%; top: 50%;
    transform: translate(-50%, -50%) rotate(-90deg);
    display: flex; align-items: center; gap: 10px;
    color: var(--brand-blue); white-space: nowrap;
  }
  .side-strip__dot { width: 34px; height: 34px; border-radius: 50%; background: var(--brand-blue); flex: none; }
  .side-strip__name {
    font-weight: 600; font-size: 15px; line-height: 1.2;
    letter-spacing: 1.5px; text-transform: uppercase;
  }
  .details { position: absolute; left: 120px; right: 0; top: 0; bottom: 0; }
  .person { padding: 28px 0 0 30px; height: 88px; border-bottom: 1.5px solid var(--rule); }
  .person__name { font-size: 26px; font-weight: 400; }
  .person__name span { color: var(--brand-blue); }
  .person__role { font-size: 12px; margin-top: 2px; }
  .contact { padding: 16px 0 0 30px; height: 96px; border-bottom: 1.5px solid var(--rule); }
  .contact__row { display: flex; align-items: center; gap: 12px; font-size: 16px; margin-bottom: 12px; }
  .contact__row svg { width: 20px; height: 20px; flex: none; }
  .social { display: flex; justify-content: space-between; padding: 16px 40px 0 30px; height: 62px; border-bottom: 1.5px solid var(--rule); font-size: 14px; }
  .social__item { display: flex; align-items: center; gap: 10px; }
  .social__dot { width: 20px; height: 20px; border-radius: 50%; }
  .social__dot--fb { background: var(--social-fb); }
  .social__dot--ig { background: var(--social-ig); }
  .write-line { position: absolute; left: 30px; right: 30px; bottom: 36px; border-bottom: 1.5px dashed var(--rule); }
</style>
</head>
<body>
  <section class="card card--brand">
    <div class="brand-lockup">
      <div class="brand-lockup__dot"></div>
      <div class="brand-lockup__name">The Harbourview<br>Motion Clinic</div>
    </div>
  </section>

  <section class="card card--details">
    <div class="side-strip">
      <div class="side-strip__lockup">
        <div class="side-strip__dot"></div>
        <div class="side-strip__name">The Harbourview<br>Motion Clinic</div>
      </div>
    </div>
    <div class="details">
      <div class="person">
        <div class="person__name">Name of <span>Person</span></div>
        <div class="person__role">Designation</div>
      </div>
      <div class="contact">
        <div class="contact__row">
          <svg viewBox="0 0 20 20" aria-hidden="true"><circle cx="10" cy="10" r="8.5" fill="none" stroke="#1c1c1c" stroke-width="1.5"/><path d="M7 6.2c.6-.4 1.2-.2 1.4.3l.6 1.3c.2.4 0 .8-.3 1l-.5.4c.4 1 1.2 1.8 2.2 2.3l.4-.5c.3-.3.7-.4 1-.2l1.3.6c.5.2.7.8.3 1.4-.6.8-1.6 1-2.6.5-2-1-3.4-2.5-4.3-4.4-.4-1-.3-2 .5-2.7z" fill="#1c1c1c"/></svg>
          555.018.2046
        </div>
        <div class="contact__row">
          <svg viewBox="0 0 20 20" aria-hidden="true"><rect x="2" y="4.5" width="16" height="11" fill="#1c1c1c"/><path d="M2 4.5l8 6 8-6" fill="none" stroke="#f3f3f1" stroke-width="1.3"/></svg>
          hello@harbourviewmotion.com
        </div>
      </div>
      <div class="social">
        <div class="social__item"><span class="social__dot social__dot--fb"></span>facebook/name</div>
        <div class="social__item"><span class="social__dot social__dot--ig"></span>instagram_name</div>
      </div>
      <div class="write-line"></div>
    </div>
  </section>
</body>
</html>
```